BUSINESS CARD - HALLORAN FIELD SERVICES

I would like to create a business card for my fertilizer spreading business. I would like to incorporate my existing logo and also a description of the services offered. The business card will be given to farmers so must be kept simple but effective. It will also be left in stores so much also be eye catching in order to stand out from other cards.

Target Market(s)

FARMERS

Requirements
Must have
• FRONT OF CARD = EXISTING LOGO + "CUSTOMISED SPREADING" below the logo

REAR Of CARD = SERVICES OFFERED AND CONTACT DETAILS

- Bulk fertilizer including Lime, Gypsum, Manure & Compost
- Granular fertilizer including Single Super, Urea, Gran-am, & Custom Blends
- Modern equipment - Autosteer & Variable Rate Capable
- Friendly & Reliable Service
- Contact Gus: 0417 552 308
Nice to have
• utilize same color scheme as existing logo

```html
<!DOCTYPE html>
<html lang="en">
<head>
<meta charset="utf-8">
<title>Halloran Field Services – Business Card</title>
<link href="https://fonts.googleapis.com/css2?family=Open+Sans:wght@600;700&family=Roboto:wght@400;500;700&display=swap" rel="stylesheet">
<style>
  :root {
    --backdrop: #d8d6d7;
    --card-white: #ffffff;
    --charcoal: #58585a;
    --text-grey: #4f4f51;
    --orange: #f7941d;
  }
  * { box-sizing: border-box; margin: 0; padding: 0; }
  html, body {
    width: 1200px; height: 1100px; overflow: hidden;
    background: var(--backdrop);
  }
  .card {
    position: absolute;
    left: 259px;
    width: 705px; height: 405px;
    border-radius: 18px;
    box-shadow: 0 2px 6px rgba(0,0,0,0.25);
    overflow: hidden;
  }
  .card--contact { top: 115px; background: var(--card-white); }
  .card--brand { top: 560px; background: var(--charcoal); }

  .contact-label {
    position: absolute; left: 42px; top: 120px;
    font: 500 26px/1 "Roboto", sans-serif;
    color: var(--text-grey);
  }
  .phone-band {
    position: absolute; left: 0; top: 158px;
    width: 316px; height: 43px;
  }
  .phone-line {
    position: absolute; left: 43px; top: 158px; height: 43px;
    display: flex; align-items: center; gap: 9px;
    font: 500 29px/1 "Roboto", sans-serif;
    color: #fff; letter-spacing: 0.5px;
  }
  .phone-line svg { width: 25px; height: 25px; }

  .brand-mark {
    position: absolute; border-radius: 50%;
  }
  .card--contact .brand-mark {
    left: 482px; top: 41px; width: 114px; height: 114px;
    background: var(--charcoal);
  }
  .brand-name {
    position: absolute; text-align: center; white-space: nowrap;
    font-family: "Roboto", sans-serif; font-weight: 700;
  }
  .card--contact .brand-name {
    left: 416px; width: 260px; top: 162px;
    font-size: 22px; color: var(--charcoal);
  }

  .services-heading {
    position: absolute; left: 42px; top: 240px;
    font: 600 25px/1 "Open Sans", sans-serif;
    color: var(--orange);
  }
  .services-list {
    position: absolute; left: 42px; top: 275px;
    list-style: none;
    font: 400 17px/24px "Roboto", sans-serif;
    color: var(--text-grey);
  }
  .services-list li::before {
    content: "•"; color: var(--orange); margin-right: 3px;
  }

  .card--brand .brand-mark {
    left: 262px; top: 52px; width: 162px; height: 162px;
    background: #ffffff;
  }
  .card--brand .brand-name {
    left: 0; width: 705px; top: 226px;
    font-size: 34px; color: #ffffff;
  }
  .tagline {
    position: absolute; left: 0; width: 705px; top: 343px;
    text-align: center;
    font: 700 23px/1 "Open Sans", sans-serif;
    color: var(--orange);
  }
</style>
</head>
<body>

<section class="card card--contact">
  <p class="contact-label">Contact Gus:</p>
  <svg class="phone-band" viewBox="0 0 316 43" aria-hidden="true">
    <polygon points="0,0 267,0 316,43 0,43" fill="var(--charcoal)"/>
  </svg>
  <p class="phone-line">
    <svg viewBox="0 0 24 24" aria-hidden="true">
      <path fill="var(--orange)" d="M6.6 10.8a15.1 15.1 0 0 0 6.6 6.6l2.2-2.2c.3-.3.7-.4 1-.2 1.1.4 2.3.6 3.6.6.6 0 1 .4 1 1V20c0 .6-.4 1-1 1A17 17 0 0 1 3 4c0-.6.4-1 1-1h3.5c.6 0 1 .4 1 1 0 1.3.2 2.5.6 3.6.1.3 0 .7-.2 1l-2.3 2.2z"/>
    </svg>
    0417 552 308
  </p>

  <div class="brand-mark" aria-hidden="true"></div>
  <p class="brand-name">Halloran Field Services</p>

  <h2 class="services-heading">SERVICES OFFERED</h2>
  <ul class="services-list">
    <li>Bulk fertilizer including Lime, Gypsum, Manure &amp; Compost</li>
    <li>Granular fertilizer including Single Super, Urea, Gran-am, &amp; Custom Blends</li>
    <li>Modern equipment - Autosteer &amp; Variable Rate Capable</li>
    <li>Friendly &amp; Reliable Service</li>
  </ul>
</section>

<section class="card card--brand">
  <div class="brand-mark" aria-hidden="true"></div>
  <p class="brand-name">Halloran Field Services</p>
  <p class="tagline">CUSTOMISED SPREADING</p>
</section>

</body>
</html>
```